Visitenkarten-Design für Sonnen-/Fensterschutz
Zielgruppe
KLW GmbH ist eine Firma, die Sonnenschutz und Fensterschutz anbieten.
'Ihr kompetenter Partner in Sachen Sonnenschutz- , Fenster- und Türtechnik. Sie erhalten echtes Handwerk aus dem Mühlviertel zu fairen Preisen.'
Unsere Zielgruppe sind Personen mit Haus, die am Land leben.
Firmenname: KLW GmbH
Slogan: Fenster & Sonnenschutz
Aufgabenstellung
Hier befindet sich das Logodesign: https://dx.qv/t-QwLpo7RbNs
Bitte ein schlichtes Design bereitstellen mit einer Dummy-Person:
Jonas Weidlinger + Telefonnummer + Email
Die finalen Daten bitte erst am Schluss berücksichtigen (für Gewinnerdesign)
Gerne auch hintern + vorne bedruckbar bereitstellen.

```html
<!DOCTYPE html>
<html lang="de">
<head>
<meta charset="utf-8">
<title>KLW GmbH – Visitenkarte</title>
<link rel="stylesheet" href="https://fonts.googleapis.com/css2?family=Barlow:wght@300;400;600;700&display=swap">
<style>
  :root {
    --paper: #ffffff;
    --ink: #2b2b2b;
    --frame: #333333;
    --band: #dd5631;
    --grad-start: #e05d2f;
    --grad-end: #d7352f;
    --brand: #e0552f;
    --canvas: #ffffff;
  }
  * { margin: 0; padding: 0; box-sizing: border-box; }
  html, body {
    width: 792px;
    height: 1200px;
    overflow: hidden;
    background: var(--canvas);
    font-family: "Barlow", Arial, sans-serif;
  }
  .sheet { position: relative; width: 792px; height: 1200px; }

  /* Front side */
  .card-front {
    position: absolute;
    left: 1px; top: 1px;
    width: 790px; height: 512px;
    background: var(--paper);
    border: 1.5px solid var(--frame);
    overflow: hidden;
  }
  .front-brand {
    position: absolute;
    right: 46px; top: 82px;
    display: flex; align-items: center; gap: 14px;
  }
  .brand-mark-square {
    width: 44px; height: 44px;
    background: var(--brand);
  }
  .front-brand .brand-name {
    font-weight: 700;
    font-size: 50px;
    line-height: 1;
    color: var(--brand);
    letter-spacing: 1px;
  }
  .contact {
    position: absolute;
    left: 50px; top: 182px;
    color: var(--ink);
    font-weight: 300;
    font-size: 38px;
    line-height: 47px;
  }
  .tagline-band {
    position: absolute;
    left: 0; right: 0; bottom: 0;
    height: 88px;
    background: var(--band);
    color: #ffffff;
    font-weight: 300;
    font-size: 27px;
    line-height: 35px;
    padding: 10px 0 0 48px;
  }

  /* Back side */
  .card-back {
    position: absolute;
    left: 2px; top: 690px;
    width: 789px; height: 510px;
    background: linear-gradient(135deg, var(--grad-start) 0%, var(--grad-end) 100%);
    display: flex; align-items: center; justify-content: center;
  }
  .back-brand {
    display: flex; align-items: center; gap: 28px;
  }
  .back-brand .brand-mark-square {
    width: 96px; height: 96px;
    background: #ffffff;
  }
  .back-brand .brand-name {
    font-weight: 700;
    font-size: 118px;
    line-height: 1;
    color: #ffffff;
    letter-spacing: 2px;
  }
</style>
</head>
<body>
<main class="sheet">
  <section class="card-front" aria-label="Vorderseite">
    <div class="front-brand">
      <span class="brand-mark-square"></span>
      <span class="brand-name">KLW GmbH</span>
    </div>
    <div class="contact">
      <p class="contact-name">Jonas Weidlinger</p>
      <p class="contact-phone">0157 98765432</p>
      <p class="contact-mail">jonas.weidlinger@postfach.de</p>
    </div>
    <div class="tagline-band">
      <p>Ihr kompetenter Partner in Sachen Sonnenschutz-,</p>
      <p>Fenster- und Türtechnik</p>
    </div>
  </section>

  <section class="card-back" aria-label="Rückseite">
    <div class="back-brand">
      <span class="brand-mark-square"></span>
      <span class="brand-name">KLW GmbH</span>
    </div>
  </section>
</main>
</body>
</html>
```